We are a local Communty Pharmacy wishing to promote and market a specialised Pharmaceutical Service

We would like a design that is professional and enticing ( according to the brief In attached files)
We wish to Market Compounding Pharmacy as a specialist side of our business.
We have the expertise a purpose built preparation laboratory.
The main purpose is an Internet presence that entices prospective patients to contact or visit our physical store.

Target Market(s)

Patients Medicos and Veterinary clients

Industry/Entity Type

Pharmacy

Coding

Coded - Design and coding required

Number of Pages Required

1 page

Requirements
Must have
• Clear friendly image
Nice to have
• soft enticing feel
Should not have
• No crass loud unprofessional elements

```html
<!DOCTYPE html>
<html lang="en">
<head>
<meta charset="utf-8">
<title>Brookvale Compounding Pharmacy</title>
<link href="https://fonts.googleapis.com/css2?family=Open+Sans:wght@400;600;700&display=swap" rel="stylesheet">
<style>
:root{
  --navy:#1f2a3a;
  --navy-dark:#151d29;
  --blue:#2f8fd0;
  --blue-deep:#1c6fae;
  --orange:#f0a020;
  --text:#666d75;
  --heading:#3a4450;
  --white:#ffffff;
}
*{margin:0;padding:0;box-sizing:border-box}
html,body{width:724px;height:1200px;overflow:hidden}
body{font-family:"Open Sans",sans-serif;color:var(--text);background:var(--white);font-size:7px;line-height:1.55;position:relative}
.topbar{height:14px;background:var(--navy);color:#aab4c0;font-size:5.5px;display:flex;align-items:center;padding:0 60px;gap:18px}
.topbar .email{margin-left:auto}
.header{height:32px;display:flex;align-items:center;padding:0 60px;border-bottom:1px solid #e6e9ec}
.brand{display:flex;align-items:center;gap:6px;font-weight:700;color:var(--blue-deep);font-size:10px}
.brand-mark{width:14px;height:14px;border-radius:50%;background:var(--orange)}
.nav{margin-left:auto;display:flex;align-items:center;gap:22px;font-size:6px;font-weight:600;color:var(--heading);letter-spacing:.3px}
.nav .search{width:16px;height:16px;border-radius:50%;background:var(--orange);display:flex;align-items:center;justify-content:center}
.hero{position:relative;height:262px;background:linear-gradient(110deg,#cfe4f4 0%,#8fbfe3 45%,#3f7fb8 100%)}
.hero-tag{position:absolute;left:0;color:var(--white);font-weight:600;letter-spacing:.8px}
.hero-tag.primary{top:112px;background:var(--orange);font-size:11px;padding:6px 16px 6px 60px}
.hero-tag.secondary{top:140px;background:var(--blue);font-size:10px;padding:6px 16px 6px 60px}
.about{position:relative;height:420px;padding:30px 60px 0}
.section-title{text-align:center;font-size:13px;font-weight:700;color:var(--heading);letter-spacing:.5px}
.rule{width:40px;height:2px;background:var(--orange);margin:5px auto 16px}
.columns{display:grid;grid-template-columns:1fr 1fr;gap:30px}
.columns p{margin-bottom:11px;font-size:7.2px}
.btn{position:absolute;left:60px;top:344px;background:var(--orange);color:var(--white);font-weight:700;font-size:6.5px;padding:8px 14px;border-radius:2px;letter-spacing:.4px}
.features{padding:0 60px}
.features h2{font-size:10px;color:var(--heading);font-weight:700;letter-spacing:.4px;border-bottom:1px solid #e3e6ea;padding-bottom:6px;margin-bottom:14px}
.cards{display:grid;grid-template-columns:repeat(3,1fr);gap:28px}
.card-img{height:104px;border-radius:2px}
.card-img.hrt{background:linear-gradient(135deg,#d9e6ef,#9fb6c6)}
.card-img.elixir{background:linear-gradient(135deg,#e7e2dc,#b8c2c9)}
.card-img.thyroid{background:linear-gradient(135deg,#e5ecf2,#a9c1d4)}
.card h3{font-size:6.5px;color:var(--blue-deep);font-weight:700;margin:10px 0 5px}
.card p{font-size:6.2px}
.footer{position:absolute;top:980px;left:0;width:724px;height:183px;background:var(--navy);padding:12px 60px;display:grid;grid-template-columns:1fr 1fr 1fr;gap:26px;color:#aab4c0}
.footer h4{color:var(--white);font-size:7.5px;font-weight:700;margin-bottom:10px;letter-spacing:.4px}
.hours td{font-size:6px;padding:3px 0;border-bottom:1px solid #2e3b4d}
.hours td:last-child{text-align:right}
.map{height:120px;background:linear-gradient(135deg,#dfe6d6,#c9d6c1)}
.contact p{font-size:6px;margin-bottom:8px}
.contact-row{display:flex;gap:6px;align-items:flex-start;font-size:6px;margin-bottom:8px}
.contact-row svg{flex:none}
.bottombar{position:absolute;top:1163px;left:0;width:724px;height:37px;background:var(--navy-dark);color:#8893a1;font-size:5.5px;display:flex;align-items:center;padding:0 60px}
.social{margin-left:auto;display:flex;align-items:center;gap:5px}
.social span{width:10px;height:10px;border-radius:50%;background:#3b4a5e;display:inline-block}
</style>
</head>
<body>
<div class="topbar">
  <span>Shop 4, 12 Harbour Street, Brookvale</span>
  <span>(08) 9000 1234</span>
  <span class="email">hello@brookvalepharmacy.example</span>
</div>
<header class="header">
  <div class="brand"><span class="brand-mark"></span>Brookvale Compounding Pharmacy</div>
  <nav class="nav">
    <span>HOME</span><span>ABOUT US</span><span>LOCATIONS</span><span>TERMS</span><span>CONTACT</span>
    <span class="search"><svg width="8" height="8" viewBox="0 0 10 10"><circle cx="4" cy="4" r="3" fill="none" stroke="#fff" stroke-width="1.4"/><line x1="6.3" y1="6.3" x2="9" y2="9" stroke="#fff" stroke-width="1.4"/></svg></span>
  </nav>
</header>
<section class="hero" role="img" aria-label="Pharmacist working with glass flasks in a compounding laboratory">
  <div class="hero-tag primary">COMPOUNDING PHARMACY</div>
  <div class="hero-tag secondary">CUSTOMISED MEDICATIONS FOR PATIENTS</div>
</section>
<section class="about">
  <h1 class="section-title">WHAT IS COMPOUNDING PHARMACY?</h1>
  <div class="rule"></div>
  <div class="columns">
    <div>
      <p>Although compounding is not new, making up medicines by hand has been part of pharmacy for centuries. Today it is enjoying renewed interest as patients and prescribers look for treatments tailored to individual needs and sensitivities, and as more people ask for medicines free of dyes, fillers or allergens.</p>
      <p>Our pharmacists prepare each formulation in a purpose built laboratory, following strict quality standards. We can change strength, remove allergens, add flavour or create a new dosage form such as a cream, gel, lozenge or liquid when a standard product is not suitable for the patient.</p>
      <p>We work closely with doctors, specialists and veterinarians so every preparation suits the person or animal who will take it.</p>
    </div>
    <div>
      <p>As a dedicated professional in our field, we are constantly updating our equipment and knowledge so that every prescription is made with care, accuracy and the latest techniques available to community pharmacy across the region.</p>
      <p>Brookvale Compounding Pharmacy is accredited under the national quality program, giving doctors, vets and patients confidence that each preparation is safe, effective and made to the highest standard in our own laboratory.</p>
      <p>Visit us in store or call our team to talk through your prescription and find the right option for you.</p>
    </div>
  </div>
  <span class="btn">READ MORE INFO</span>
</section>
<section class="features">
  <h2>FEATURE ITEMS</h2>
  <div class="cards">
    <article class="card"><div class="card-img hrt" role="img" aria-label="Pharmacist preparing capsules"></div><h3>SAMPLE HRT ARTICLE</h3><p>We make hormone creams in exact strengths to suit each patient's needs.</p></article>
    <article class="card"><div class="card-img elixir" role="img" aria-label="Veterinary patient receiving medicine"></div><h3>SAMPLE ELIXIR THERAPY</h3><p>Flavoured liquids and chews help pets take the medicine they need.</p></article>
    <article class="card"><div class="card-img thyroid" role="img" aria-label="Doctor checking a patient's thyroid"></div><h3>SAMPLE THYROID EXTRACT</h3><p>Thyroid doses prepared precisely for patients who need a tailored strength.</p></article>
  </div>
</section>
<footer class="footer">
  <div>
    <h4>PHARMACY HOURS</h4>
    <table class="hours" style="width:100%;border-collapse:collapse">
      <tr><td>Monday</td><td>9:00 am – 5:30 pm</td></tr>
      <tr><td>Tuesday</td><td>9:00 am – 5:30 pm</td></tr>
      <tr><td>Wednesday</td><td>9:00 am – 5:30 pm</td></tr>
      <tr><td>Thursday</td><td>9:00 am – 7:00 pm</td></tr>
      <tr><td>Friday</td><td>9:00 am – 5:30 pm</td></tr>
      <tr><td>Saturday</td><td>9:00 am – 1:00 pm</td></tr>
    </table>
  </div>
  <div>
    <h4>LOCATIONS</h4>
    <div class="map" role="img" aria-label="Street map showing the pharmacy location"></div>
  </div>
  <div class="contact">
    <h4>CONTACT INFO</h4>
    <p>For any compounding enquiry, our team is happy to help by phone or email.</p>
    <div class="contact-row"><svg width="7" height="9" viewBox="0 0 10 13"><path d="M5 0C2.2 0 0 2.2 0 5c0 3.7 5 8 5 8s5-4.3 5-8c0-2.8-2.2-5-5-5z" fill="#f0a020"/><circle cx="5" cy="5" r="1.8" fill="#1f2a3a"/></svg><span>Shop 4, 12 Harbour Street, Brookvale</span></div>
    <div class="contact-row"><svg width="8" height="8" viewBox="0 0 10 10"><path d="M2 0l2 2.5-1 1.2c.6 1.3 1.6 2.3 2.9 2.9l1.2-1L10 8 8.5 10C4 9.5.5 6 0 1.5z" fill="#f0a020"/></svg><span>(08) 9000 1234</span></div>
    <div class="contact-row"><svg width="8" height="7" viewBox="0 0 10 8"><rect width="10" height="8" rx="1" fill="#f0a020"/><path d="M0 1l5 3.5L10 1" fill="none" stroke="#1f2a3a" stroke-width="1"/></svg><span>hello@brookvalepharmacy.example</span></div>
  </div>
</footer>
<div class="bottombar">
  <span>© 2024 Brookvale Pharmacy. All rights reserved.</span>
  <div class="social">Connect with our social networks <span></span><span></span><span></span></div>
</div>
</body>
</html>
```